Kestrel Motion LLC Sports Therapy and Soft Tissue Injury solutions

We are a company that specializes in Sports Therapy, Physical therapy, muscular rehab, nutrition plans, and personal training. Kestrel Motion travels around the country and world treating athletes and people in the workforce that have Soft Tissue injuries. We are legally partnered with VMR(Vantor Muscle Recovery/vantorrecovery.example) in treating endurance athletes ex. SteelRidge triathalon. We educate our patients on how to sustain a healthy lifestyle.We need a web design that has a Home page summarizing our services, a Physical therapy page, a Personal training and nutrition page. Our ultimate goal is to build relationships with fitness centers, training facilities, and companies that are implementing preventative health measures for their employees. We want to incorporate the VMR logo and Steelridge logo attached in the website but, we want to use our own name (Kestrel Motion LLC) as the main draw. We will provide literature for the website.

Target Market(s)

Grindlane training gyms, Fitness centers, Dance studios, Companies looking for Corporate Wellness programs

Industry/Entity Type

Health And Wellness

Number of Pages Required

4 page

Font styles to use
Sans Serif

Requirements
Must have
• Stock Photos of Athletes training. Examples of Endurance Athletes and Cross training. A mesh of as many sports and training methods as possible. We are a new company and don't have many photos. Easy accessibility to change and add text as the company grows. Vantor Muscle recovery logo incorporated in the back ground of the website. Always visible but does not take over the web page
Nice to have
• Sleek and cool, and masculine design. We want the website to stand out without focusing on one individual. We want to use the website to brand the company (Kestrel Motion LLC) with easy access to social media platforms

```html
<!DOCTYPE html>
<html lang="en">
<head>
<meta charset="utf-8">
<title>Kestrel Motion LLC — Physical Therapy</title>
<link rel="stylesheet" href="https://fonts.googleapis.com/css2?family=Anton&family=Open+Sans:wght@400;600;700&display=swap">
<style>
  :root {
    --ink: #2b2b2b;
    --text: #333333;
    --red: #cc0a0a;
    --nav-bg: #161616;
    --footer-bg: #141414;
    --band: #f7f7f7;
    --rule: #e6e6e6;
    --muted: #b9b9b9;
    --input: #2c2c2c;
    --white: #ffffff;
  }
  * { box-sizing: border-box; margin: 0; padding: 0; }
  html, body { width: 1200px; height: 2553px; overflow: hidden; }
  body { position: relative; background: var(--white); font-family: "Open Sans", sans-serif; color: var(--text); }

  /* Header */
  .site-header { position: absolute; left: 0; top: 0; width: 1200px; height: 66px; background: var(--nav-bg); }
  .brand { position: absolute; left: 160px; top: 18px; font: 700 20px/28px "Open Sans", sans-serif; color: var(--white); }
  .main-nav a { position: absolute; top: 26px; font: 400 11px/14px "Anton", sans-serif; color: var(--white); text-decoration: none; letter-spacing: .3px; }
  .main-nav a.active::after { content: ""; position: absolute; left: 50%; bottom: -26px; width: 22px; height: 3px; margin-left: -11px; background: var(--red); }

  /* Hero */
  .hero { position: absolute; left: 0; top: 66px; width: 1200px; height: 453px;
    background: linear-gradient(90deg, #5c5c5c 0%, #6e6e6e 35%, #7a7a7a 60%, #5e5e5e 100%); }
  .hero-shade { position: absolute; inset: 0; background: rgba(20,20,20,.35); }
  .hero h1 { position: absolute; left: 0; width: 1200px; top: 162px; text-align: center; font: 400 38px/46px "Anton", sans-serif; color: var(--white); letter-spacing: .5px; }
  .hero p { position: absolute; left: 330px; width: 540px; top: 218px; text-align: center; font: 600 15px/24px "Open Sans", sans-serif; color: var(--white); }

  /* Feature rows */
  .feature-title { position: absolute; font: 400 24px/36px "Anton", sans-serif; color: var(--ink); letter-spacing: .6px; }
  .feature-title em { font-style: normal; color: var(--red); }
  .body-copy { position: absolute; font: 400 10.4px/22px "Open Sans", sans-serif; color: var(--text); }
  .photo { position: absolute; }

  /* Service band */
  .service-band { position: absolute; left: 0; top: 1357px; width: 1200px; height: 531px; background: var(--band); border-top: 1px solid var(--rule); border-bottom: 1px solid var(--rule); }
  .service-card { position: absolute; top: 98px; width: 272px; text-align: center; }
  .service-card .photo { position: relative; width: 272px; height: 203px; }
  .service-card h3 { margin-top: 24px; font: 400 16px/22px "Anton", sans-serif; color: var(--red); }
  .service-card p { margin: 10px auto 0; width: 262px; font: 400 10.6px/20px "Open Sans", sans-serif; color: var(--text); }

  /* Call to action */
  .cta-title { position: absolute; left: 0; top: 1955px; width: 1200px; text-align: center; font: 400 24px/36px "Anton", sans-serif; color: var(--ink); letter-spacing: .5px; }
  .cta-title em { font-style: normal; color: var(--red); }
  .cta-copy { position: absolute; left: 230px; top: 2014px; width: 740px; text-align: center; font: 400 10.6px/22px "Open Sans", sans-serif; }
  .cta-button { position: absolute; left: 536px; top: 2104px; width: 128px; height: 41px; background: var(--red); color: var(--white); text-align: center; font: 400 12px/41px "Anton", sans-serif; letter-spacing: .4px; }

  /* Footer */
  .site-footer { position: absolute; left: 0; top: 2197px; width: 1200px; height: 356px; background: var(--footer-bg); color: var(--white); }
  .signup-title { position: absolute; left: 163px; top: 39px; font: 400 22px/32px "Anton", sans-serif; letter-spacing: .6px; }
  .signup-input { position: absolute; left: 621px; top: 36px; width: 329px; height: 41px; background: var(--input); color: var(--muted); font: 400 11px/41px "Open Sans", sans-serif; padding-left: 12px; }
  .signup-button { position: absolute; left: 950px; top: 36px; width: 88px; height: 41px; background: var(--red); text-align: center; font: 400 13px/41px "Anton", sans-serif; }
  .footer-rule { position: absolute; left: 162px; top: 109px; width: 876px; height: 1px; background: #2e2e2e; }
  .footer-col { position: absolute; top: 150px; }
  .footer-col h4 { font: 400 11px/16px "Anton", sans-serif; letter-spacing: .3px; margin-bottom: 14px; }
  .footer-col li { list-style: none; font: 400 12px/22px "Open Sans", sans-serif; color: var(--muted); }
  .legal { position: absolute; left: 162px; top: 315px; font: 400 11px/16px "Open Sans", sans-serif; color: var(--muted); }
  .social { position: absolute; left: 860px; top: 313px; display: flex; gap: 18px; }
  .social span { width: 14px; height: 14px; border-radius: 50%; background: var(--white); }
</style>
</head>
<body>

<header class="site-header">
  <div class="brand">Kestrel Motion LLC</div>
  <nav class="main-nav">
    <a style="left:489px">HOME</a>
    <a style="left:557px">SERVICES</a>
    <a class="active" style="left:641px">PHYSICAL THERAPY</a>
    <a style="left:765px">PERSONAL TRAINING</a>
    <a style="left:896px">NUTRITION</a>
    <a style="left:983px">CONTACT US</a>
  </nav>
</header>

<section class="hero" role="img" aria-label="Therapist guiding an older woman through an arm exercise in a bright gym">
  <div class="hero-shade"></div>
  <h1>PHYSICAL THERAPY</h1>
  <p>Sed ut perspiciatis unde omnloreis isteit voluaccusantium doloremue lauloredantiumtota mrem aperiameaue sa lauloredub illo.</p>
</section>

<section class="feature-row">
  <h2 class="feature-title" style="left:162px;top:603px">EVERYONE HAS A<br>REASON FOR <em>PHYSICAL THERAPY</em></h2>
  <p class="body-copy" style="left:162px;top:690px;width:445px">Sed ut perspiciatis unde omnis iste natus sitolu ptatem accusantium doloremque lantium, totme maperiam, eaque ipsa quae ab illo inventore veritati quasi archite ed ut perspiciatis unde omnis iste natus sitolu ptatem accusantium doloremque laudant ium,totmem aperi amaque ipsa quae ab illo inventore veritati quasiar hit ecterspiciatis unde omnis iste natus sitolu.maque ipsa quae ab illo inventoretotme maperiam, eaque ipsa quae ab illo invntore veritati quasi archite ed ut perspiciatis unde omnis iste natus sitolu ptatem accusantium doloremque laudant ium.totmem aperi amaque ipsa quae ab illo inventore veritati qsia hit ecterspiciatis unde omnis iste natus sitolu.maque ipsa quae ab illo inventore.</p>
  <div class="photo" role="img" aria-label="Therapist applying pink and blue kinesiology tape to a knee" style="left:671px;top:596px;width:367px;height:284px;background:linear-gradient(135deg,#e9e4e2 0%,#d8b6a6 45%,#3f4a5c 75%,#c99a84 100%)"></div>
</section>

<section class="feature-row">
  <div class="photo" role="img" aria-label="Physiotherapist stretching an older woman's arm in a clinic" style="left:162px;top:980px;width:366px;height:285px;background:linear-gradient(120deg,#c9d6e3 0%,#d9a7a3 40%,#7fa3c9 75%,#dfe6ee 100%)"></div>
  <h2 class="feature-title" style="left:596px;top:988px">TEAM TRAINING<br>CONNECTS YOU <em>WITH OTHERS</em></h2>
  <p class="body-copy" style="left:596px;top:1075px;width:447px">Sed ut perspiciatis unde omnis iste natus sitolu ptatem accusantium doloremque lantium, totme maperiam, eaque ipsa quae ab illo inventore veritati quasi archite ed ut perspiciatis unde omnis iste natus sitolu ptatem accusantium doloremque laudant ium,totmem aperi amaque ipsa quae ab illo inventore veritati quasiar hit ecterspiciatis unde omnis iste natus sitolu.maque ipsa quae ab illo inventoretotme maperiam, eaque ipsa quae ab illo invntore veritati quasi archite ed ut perspiciatis unde omnis iste natus sitolu ptatem accusantium doloremque laudant ium.totmem aperi amaque ipsa quae ab illo inventore veritati qsia hit ecterspiciatis unde omnis iste natus sitolu.maque ipsa quae ab illo inventore.</p>
</section>

<section class="service-band">
  <article class="service-card" style="left:162px">
    <div class="photo" role="img" aria-label="Trainer coaching a woman doing push-ups on dumbbells in a gym" style="background:linear-gradient(135deg,#4a4a4a 0%,#8a8580 45%,#c9c4bd 70%,#5a6a80 100%)"></div>
    <h3>Finibus Bonorum et Maloru perspi</h3>
    <p>Sed ut perspiciatis unde omnis iste natuslor sitolu ptatem accusantium doloremque laudantium, totm e maperiam, eaque ipsa quaeilloed ut perspiciatis unde omnis iste natus sitolu ptatem.</p>
  </article>
  <article class="service-card" style="left:465px">
    <div class="photo" role="img" aria-label="Massage therapist working on a client's shoulders" style="background:linear-gradient(135deg,#d9d4cf 0%,#b07a58 45%,#8a5a3e 70%,#e8e4df 100%)"></div>
    <h3>Finibus Bonorum et Malorum</h3>
    <p>Sed ut perspiciatis unde omnis iste natuslor sitolu ptatem accusantium doloremque laudantium, totm e maperiam, eaque ipsa quaeilloed ut perspiciatis unde omnis iste natus sitolu ptatem .</p>
  </article>
  <article class="service-card" style="left:766px">
    <div class="photo" role="img" aria-label="Therapist stretching a client's leg on a treatment table" style="background:linear-gradient(135deg,#3e3a36 0%,#9a8a7a 40%,#d9cfc3 65%,#4f6e8a 100%)"></div>
    <h3>Finibus Bonorum et Malorum</h3>
    <p>Sed ut perspiciatis unde omnis iste natuslor sitolu ptatem accusantium doloremque laudantium, totm e maperiam, eaque ipsa quaeilloed ut perspiciatis unde omnis iste natus sitolu ptatem .</p>
  </article>
</section>

<section class="cta">
  <h2 class="cta-title">VIRTUAL FITNESS CLASSES GIVE YOU <em>FITNESS CLASSES</em></h2>
  <p class="cta-copy">Sed ut perspiciatis unde omnis iste natus sitolu ptatem accusantium doloremque lantium, totme maperiam, eaque ipsa quae ab illo inventore veritati quasi archite ed ut perspiciatis unde omnis iste natus sitolu ptatem accusantium doloremque laudant ium,totmem aperi amaque ipsa quae ab illo inventore veritati quasiar hit ecterspiciatis unde omnis iste natus sitolu.maque ipsa quae ab illo inventoretotme maperia eaqu ipsa.</p>
  <div class="cta-button">GET STARTED HERE</div>
</section>

<footer class="site-footer">
  <h2 class="signup-title">SIGN UP FOR THE LATEST NEWS AND OFFERS</h2>
  <div class="signup-input">Enter Email Address:</div>
  <div class="signup-button">SIGN UP</div>
  <div class="footer-rule"></div>

  <div class="footer-col" style="left:162px">
    <h4>FOR CONSUMERS</h4>
    <ul><li>Disclosures</li><li>Investor Relations</li><li>Corporate Governance</li><li>Newsroom</li></ul>
  </div>
  <div class="footer-col" style="left:364px">
    <h4>BUSINESS</h4>
    <ul><li>Partners</li><li>Blog</li><li>Company</li><li>Resources</li></ul>
  </div>
  <div class="footer-col" style="left:529px">
    <h4>COMPANY</h4>
    <ul><li>Nutrition</li><li>Dietary Science</li><li>Recipe/Food Prep</li><li>Training</li></ul>
  </div>
  <div class="footer-col" style="left:708px">
    <h4>HELP</h4>
    <ul><li>Terms</li><li>Privacy</li><li>Contact us</li></ul>
  </div>
  <div class="footer-col" style="left:860px">
    <h4>CONTACT US FOR PROGRAMS</h4>
    <ul><li>2250 W. Ardent Ave Suite 410</li><li>Harbor Vale, California, 90715</li><li>Phone: (555)014-2290</li></ul>
  </div>

  <p class="legal">© 2017 Kestrel Motion LLC. All Copyrights are Reserved. Terms of Use.Certification # 30917</p>
  <div class="social" role="img" aria-label="Social media links">
    <span></span><span></span><span></span><span></span><span></span><span></span>
  </div>
</footer>

</body>
</html>
```